Website for new dental office

I am Dr. Colin Ashford and am building a new dental practice. I specialize in general dentistry. I am young and have a higher end dental practice incorporating very new technologies and would like my website to reflect that. As many dental patients are older, the website must be very easy to navigate. I would like patients to be able to request appointments, and will eventually add on patient information forms (the health history, etc, that you normally fill out in the practice) from my practice management software, so leave an area for that.

Industry/Entity Type

Building

```html
<!DOCTYPE html>
<html lang="en">
<head>
<meta charset="utf-8">
<title>Colin Ashford, DDS — Contact</title>
<link href="https://fonts.googleapis.com/css2?family=Open+Sans:wght@400;600;700&family=Raleway:wght@400;500&display=swap" rel="stylesheet">
<style>
  :root{
    --brand:#1f63a8;
    --brand-light:#2a8ae0;
    --nav-top:#3a92e0;
    --nav-bottom:#1a64b8;
    --nav-active:#1a4d92;
    --ink:#333a40;
    --muted:#7a7f85;
    --line:#e3e6e9;
    --orange:#f7661c;
    --orange-light:#ffa42e;
    --panel:#f5f5f5;
  }
  *{box-sizing:border-box;margin:0;padding:0}
  html,body{width:1165px;height:1200px;overflow:hidden;background:#fff}
  body{font-family:"Open Sans",Arial,sans-serif;color:var(--ink)}
  .page{position:relative;width:1165px;height:1200px;overflow:hidden}

  .site-header{position:absolute;left:0;top:0;width:100%;height:114px;
    background:linear-gradient(#d9ebfb,#ffffff)}
  .brand-name{position:absolute;left:105px;top:38px;font-size:33px;font-weight:600;color:var(--brand-light);letter-spacing:.3px}
  .header-phone{position:absolute;right:115px;top:36px;display:flex;align-items:center;gap:10px;font-size:27px;color:#444}

  .main-nav{position:absolute;left:0;top:114px;width:100%;height:42px;
    background:linear-gradient(var(--nav-top),var(--nav-bottom))}
  .main-nav ul{list-style:none;position:absolute;left:0;top:0;height:42px}
  .main-nav li{position:absolute;top:0;height:42px;line-height:42px;color:#fff;font-size:15px;text-align:center}
  .main-nav li.sep::before{content:"";position:absolute;left:0;top:9px;height:24px;border-left:1px solid rgba(255,255,255,.25)}
  .main-nav li.home{font-weight:700}
  .main-nav li.active{background:var(--nav-active)}

  .hero{position:absolute;left:0;top:156px;width:100%;height:246px;
    background:linear-gradient(90deg,#d6dee6 0%,#eef2f6 40%,#fafbfc 60%);border-bottom:1px solid #d3e3f2}
  .hero-photo{position:absolute;right:0;top:0;width:590px;height:246px;
    background:linear-gradient(90deg,rgba(250,251,252,0) 0%,#ead8cc 45%,#d9b7a2 70%,#f3ece7 100%)}
  .hero h1{position:absolute;left:106px;top:60px;font-size:57px;font-weight:600;color:var(--brand);letter-spacing:-.5px}
  .hero p{position:absolute;left:108px;top:134px;width:470px;font-size:20px;line-height:26px;color:#2a2f34}

  .section-title{position:absolute;left:107px;top:446px;width:938px;height:30px}
  .section-title h2{font-family:"Raleway",sans-serif;font-weight:400;font-size:25px;color:var(--brand-light);position:absolute;left:0;top:0}
  .section-title .rule{position:absolute;left:127px;top:15px;width:811px;border-top:1px dotted #b9bec3}
  .section-title .rule-accent{position:absolute;left:127px;top:14px;width:112px;height:3px;background:var(--brand-light)}

  .card{position:absolute;border:1px solid var(--line);background:#fff}
  .card h3{font-family:"Raleway",sans-serif;font-weight:400;font-size:21px;color:#3c4248;display:flex;align-items:center;gap:8px}

  .contact-form{left:108px;top:507px;width:584px;height:429px;padding:14px 21px}
  .contact-form h3{margin-bottom:12px}
  .field{border:1px solid var(--line);height:38px;margin-bottom:19px;padding:10px 11px;font-size:12px;color:var(--muted)}
  .field.message{height:171px;position:relative}
  .submit{display:inline-block;background:var(--orange);color:#fff;font-size:14px;padding:6px 11px}

  .find-us{left:768px;top:506px;width:276px;height:228px;padding:14px 15px}
  .opening-hours{left:768px;top:756px;width:276px;height:211px;padding:14px 15px}
  .info-list{list-style:none;margin-top:16px;font-family:"Raleway",sans-serif;font-size:14px;color:#333}
  .info-list li{display:flex;align-items:center;gap:11px;height:31.5px}
  .info-list svg{width:12px;flex:0 0 12px}
  .hours-list{list-style:none;margin-top:16px;padding-left:15px;font-family:"Raleway",sans-serif;font-size:13.5px;color:#333}
  .hours-list li{height:28.2px;display:flex;align-items:center;gap:9px}
  .hours-list li::before{content:"";width:6px;height:6px;border-radius:50%;background:#555}

  .cta{position:absolute;left:108px;top:989px;width:951px;height:100px;background:var(--panel);border:1px solid #e2e2e2;border-radius:6px}
  .cta p{position:absolute;left:34px;top:33px;font-size:26px;color:#555}
  .cta-button{position:absolute;right:26px;top:22px;width:208px;height:58px;border-radius:3px;
    background:linear-gradient(var(--orange-light),var(--orange));color:#fff;font-size:19px;font-weight:600;
    display:flex;align-items:center;justify-content:space-between;padding:0 10px 0 8px}

  .site-footer{position:absolute;left:0;top:1131px;width:100%;text-align:center;font-family:"Raleway",sans-serif;font-size:13.5px;color:#222}
</style>
</head>
<body>
<div class="page">
  <header class="site-header">
    <div class="brand-name">Colin Ashford, DDS</div>
    <div class="header-phone">
      <svg width="40" height="40" viewBox="0 0 40 40" aria-hidden="true">
        <circle cx="24" cy="16" r="13" fill="none" stroke="#2a8ae0" stroke-width="2"/>
        <text x="24" y="21" font-size="13" font-weight="700" fill="#2a8ae0" text-anchor="middle" font-family="Open Sans,sans-serif">24</text>
        <path d="M4 8c2-3 6-3 7 0l2 5c1 2-1 3-2 4 1 4 4 8 8 10 1-1 2-3 4-2l5 2c3 1 3 5 0 7-6 4-15-2-20-9C3 19 1 12 4 8z" fill="#2b3440"/>
      </svg>
      <span>+123 2345 4567</span>
    </div>
  </header>

  <nav class="main-nav">
    <ul>
      <li class="home" style="left:90px;width:82px">HOME</li>
      <li class="sep" style="left:188px;width:130px">ABOUT US</li>
      <li class="sep" style="left:318px;width:127px">SERVICES</li>
      <li class="sep" style="left:445px;width:141px">RESOURCES</li>
      <li class="sep" style="left:586px;width:119px">GALLERY</li>
      <li class="sep" style="left:705px;width:104px">CASES</li>
      <li class="sep" style="left:809px;width:105px">TEAM</li>
      <li class="active" style="left:914px;width:113px">CONTACT</li>
    </ul>
  </nav>

  <section class="hero">
    <div class="hero-photo" role="img" aria-label="Photo of smiling receptionists wearing headsets"></div>
    <h1>Contact</h1>
    <p>Lorem Ipsum is simply dummy text of the printing and typesetting industry. Lorem Ipsum has been</p>
  </section>

  <div class="section-title">
    <h2>Contact Us</h2>
    <div class="rule"></div>
    <div class="rule-accent"></div>
  </div>

  <section class="card contact-form">
    <h3>
      <svg width="30" height="30" viewBox="0 0 30 30" aria-hidden="true">
        <circle cx="15" cy="9" r="6" fill="#222"/>
        <path d="M3 29c0-8 5-12 12-12s12 4 12 12z" fill="#222"/>
      </svg>
      Get In Touch
    </h3>
    <div class="field">Your Name *</div>
    <div class="field">E-mail address *</div>
    <div class="field message">Message *</div>
    <span class="submit">Submit</span>
  </section>

  <section class="card find-us">
    <h3>
      <svg width="14" height="18" viewBox="0 0 14 18" aria-hidden="true"><path d="M7 1a5 5 0 0 1 5 5c0 4-5 8-5 8S2 10 2 6a5 5 0 0 1 5-5z" fill="none" stroke="#333" stroke-width="2"/><circle cx="7" cy="6" r="1.8" fill="#333"/><path d="M1 17h12" stroke="#333" stroke-width="2"/></svg>
      Find Us
    </h3>
    <ul class="info-list">
      <li><svg viewBox="0 0 12 12"><path d="M6 1a3.5 3.5 0 0 1 3.5 3.5C9.5 7 6 11 6 11S2.5 7 2.5 4.5A3.5 3.5 0 0 1 6 1z" fill="#333"/><circle cx="6" cy="4.5" r="1.2" fill="#fff"/></svg>Location: 123 Road Abc Street NY</li>
      <li><svg viewBox="0 0 12 12"><rect x="1" y="2" width="10" height="9" fill="none" stroke="#333" stroke-width="1.4"/><path d="M1 5h10" stroke="#333" stroke-width="1.4"/></svg>Hours: Monday - Friday, 0900 - 18:00</li>
      <li><svg viewBox="0 0 12 12"><rect x="3.5" y="1.5" width="5" height="9" rx="1" fill="none" stroke="#333" stroke-width="1.3"/></svg>Mobile: 123 456 7890</li>
      <li><svg viewBox="0 0 12 12"><path d="M2 2c1-1 2-1 2.5 0l1 2c.3.7-.2 1-.7 1.5.6 1.3 1.5 2.2 2.8 2.8.5-.5.8-1 1.5-.7l2 1c1 .5 1 1.5 0 2.5C8 13 0 5 2 2z" fill="#333"/></svg>Telephone: 123 456 7</li>
      <li><svg viewBox="0 0 12 12"><rect x="1" y="2.5" width="10" height="7" fill="#333"/><path d="M1 3l5 3.5L11 3" fill="none" stroke="#fff" stroke-width="1"/></svg>Email: care@ashfordsmile.com</li>
    </ul>
  </section>

  <section class="card opening-hours">
    <h3>
      <svg width="22" height="22" viewBox="0 0 22 22" aria-hidden="true"><circle cx="11" cy="11" r="9" fill="none" stroke="#333" stroke-width="1.8"/><path d="M11 5v6l4 3" fill="none" stroke="#333" stroke-width="1.8"/></svg>
      Opening Hours
    </h3>
    <ul class="hours-list">
      <li>Monday 9:00am-5:00pm Tuesday</li>
      <li>9:00am-6:00pmWednesday 9:00am</li>
      <li>5:00pmThursday 9:00am –</li>
      <li>5:00pmFriday 9:00am –</li>
      <li>5:00pmSaturday and evenings- By</li>
    </ul>
  </section>

  <section class="cta">
    <p>Want to Get Treated? Schedule Your Appointment Now!</p>
    <div class="cta-button">
      <span>Get Appointment</span>
      <svg width="26" height="26" viewBox="0 0 26 26" aria-hidden="true">
        <rect x="2" y="4" width="22" height="20" fill="none" stroke="#2b3440" stroke-width="2"/>
        <path d="M7 1v6M19 1v6" stroke="#2b3440" stroke-width="2"/>
        <g fill="#2b3440"><rect x="6" y="10" width="3" height="3"/><rect x="11.5" y="10" width="3" height="3"/><rect x="17" y="10" width="3" height="3"/><rect x="6" y="16" width="3" height="3"/><rect x="11.5" y="16" width="3" height="3"/><rect x="17" y="16" width="3" height="3"/></g>
      </svg>
    </div>
  </section>

  <footer class="site-footer">© Copyrights 2014 All rights Reserved</footer>
</div>
</body>
</html>
```